Landscaping flier 2024

Create a 1 page flier for landscaping services
1. Must be completed in Adobe Photoshop
2. Size 8.5" x 11" (portrait layout)
3. Include logo
4. Text to include:
2024 Gravesite Landscaping Packages
info@hollowbrookmemorial.org
(201) 555-0148
hollowbrookmemorial.org
5. Use chart text for the content. DO NOT COPY THE CHART DESIGN/FORMAT. Use the chart for the text you need only.
6. Use "Pricing cards as format for laying out the chart". Open to other ideas as well.
**Use the example of chart design (handwritten) to base your design off of.
7. Photos
-include before and after care photos

```html
<!DOCTYPE html>
<html lang="en">
<head>
<meta charset="utf-8">
<title>2024 Gravesite Landscaping Packages</title>
<link rel="stylesheet" href="https://fonts.googleapis.com/css2?family=Libre+Baskerville:wght@400;700&family=Montserrat:wght@400;500;600;700;800&display=swap">
<style>
:root{
  --bg:#e8e8e8;
  --paper:#ffffff;
  --wine:#8e1f33;
  --wine-bright:#a3203d;
  --wine-dark:#6e1627;
  --navy:#233344;
  --navy-dark:#1b2937;
  --blue:#35587f;
  --blue-dark:#26405f;
  --gold:#e3b64a;
  --tick:#6cc04a;
  --cross:#e2474b;
  --ink:#2b2b2b;
  --muted:#666e78;
  --grass:#6f9a3c;
}
*{box-sizing:border-box;margin:0;padding:0}
html,body{width:1200px;height:2415px;overflow:hidden;background:var(--bg)}
body{font-family:"Montserrat",sans-serif;position:relative}
.flier{position:absolute;left:0;top:431px;width:1200px;height:1553px;background:var(--paper);overflow:hidden;box-shadow:0 6px 24px rgba(0,0,0,.12)}
.headline{position:absolute;top:48px;left:0;width:100%;text-align:center;font-family:"Libre Baskerville",serif;font-weight:700;color:var(--wine);text-transform:uppercase;line-height:1.55}
.headline .line1{font-size:44px;display:block}
.headline .line2{font-size:46px;display:block;letter-spacing:.5px}
.headline-rule{position:absolute;top:166px;left:420px;width:360px;height:2px;background:var(--wine)}
.hero-photo{position:absolute;top:180px;left:0;width:100%;height:340px;background:linear-gradient(180deg,#dfe6e8 0%,#c9c48a 25%,#9aa35a 45%,#5f6e49 70%,#3e4a3a 100%)}
.band{position:absolute;top:505px;left:0;width:100%;height:60px}
.card{position:absolute;color:#fff;display:flex;flex-direction:column;box-shadow:0 4px 10px rgba(0,0,0,.2)}
.card--seasonal{left:50px;top:530px;width:360px;height:700px;background:var(--navy)}
.card--perpetual{left:410px;top:480px;width:380px;height:780px;background:var(--wine-bright);z-index:2}
.card--basic{left:790px;top:530px;width:360px;height:700px;background:var(--navy)}
.card__head{padding:26px 20px 34px;text-align:center;background:linear-gradient(180deg,var(--blue) 0%,var(--blue-dark) 100%);clip-path:polygon(0 0,100% 0,100% 82%,50% 100%,0 82%)}
.card--perpetual .card__head{background:linear-gradient(180deg,#b3294a 0%,var(--wine) 100%);padding-top:40px}
.card__title{font-size:27px;font-weight:800;line-height:1.05;text-transform:uppercase}
.card__sub{font-size:11px;font-weight:500;text-transform:uppercase;margin-top:8px;line-height:1.35;opacity:.9}
.ribbon{position:absolute;left:-6px;top:14px;background:var(--gold);color:var(--wine-dark);font-size:10px;font-weight:800;padding:4px 14px;transform:rotate(-25deg);text-transform:uppercase}
.price{display:flex;align-items:center;justify-content:center;gap:12px;padding:22px 16px 6px}
.price__label{font-size:12px;font-weight:600;text-transform:uppercase;line-height:1.3;text-align:right}
.price__amount{font-size:52px;font-weight:600;line-height:1}
.price__amount sup{font-size:22px;vertical-align:top;position:relative;top:4px}
.price__note{text-align:center;font-size:13px;opacity:.85;padding-bottom:22px}
.terms{display:flex;gap:10px;align-items:center;justify-content:center}
.term{display:flex;flex-direction:column;align-items:center}
.term__circle{width:46px;height:46px;border-radius:50%;background:var(--blue);display:flex;flex-direction:column;align-items:center;justify-content:center;font-weight:800;font-size:19px;line-height:1}
.term__circle small{font-size:7px;font-weight:600;text-transform:uppercase}
.term__cost{font-size:14px;font-weight:700;margin-top:4px}
.term__cost sup{font-size:8px}
.terms__note{font-size:12px;line-height:1.3;max-width:92px;margin-left:8px}
.schedule{display:flex;gap:14px;align-items:center;padding:14px 18px;background:rgba(0,0,0,.2);border-top:1px solid rgba(255,255,255,.15)}
.schedule__label{font-size:10px;font-weight:800;text-transform:uppercase;line-height:1.25;flex:0 0 96px}
.schedule__text{font-size:11px;line-height:1.35;opacity:.9}
.features{list-style:none;padding:24px 24px 0 36px}
.features li{position:relative;padding-left:24px;font-size:16px;line-height:1.25;margin-bottom:19px}
.features li::before{content:"";position:absolute;left:0;top:3px;width:13px;height:13px;border-radius:50%;background:var(--cross)}
.features li.is-included::before{background:var(--tick)}
.brand{position:absolute;left:80px;top:1320px;display:flex;align-items:center;gap:16px;font-family:"Libre Baskerville",serif;font-size:30px;color:var(--wine);text-transform:uppercase;letter-spacing:.5px}
.brand__dot{width:22px;height:22px;border-radius:50%;background:var(--wine)}
.contact{position:absolute;left:140px;top:1395px;list-style:none}
.contact li{display:flex;align-items:center;gap:16px;font-size:20px;color:var(--ink);margin-bottom:18px}
.contact li.phone{font-weight:700;font-size:22px}
.contact svg{width:18px;height:18px;flex:none}
.proof{position:absolute;top:1330px;width:230px;height:176px}
.proof--before{left:680px}
.proof--after{left:930px}
.proof__photo{width:100%;height:100%;background:linear-gradient(180deg,#c9d0c9 0%,#7f9a58 35%,var(--grass) 70%,#4f7a2b 100%)}
.proof__tag{position:absolute;top:-12px;left:50%;transform:translateX(-50%);background:var(--wine);color:#fff;font-size:14px;font-style:italic;font-weight:600;padding:5px 16px;white-space:nowrap}
</style>
</head>
<body>
<main class="flier">
  <h1 class="headline"><span class="line1">2024 Gravesite</span><span class="line2">Landscaping Packages</span></h1>
  <div class="headline-rule"></div>

  <div class="hero-photo" role="img" aria-label="Photo of a cemetery lawn with headstones, autumn trees and a historic building"></div>
  <svg class="band" viewBox="0 0 1200 60" preserveAspectRatio="none" aria-hidden="true">
    <polygon points="0,20 1200,0 1200,30 0,60" fill="#233344"/>
    <polygon points="0,15 420,10 420,40 0,45" fill="#8e1f33"/>
  </svg>

  <section class="card card--seasonal">
    <header class="card__head">
      <h2 class="card__title">Seasonal Care</h2>
      <p class="card__sub">Seasonal landscaping<br>grave care</p>
    </header>
    <div class="price">
      <div class="terms">
        <div class="term"><div class="term__circle">1<small>year</small></div><div class="term__cost"><sup>$</sup>132</div></div>
        <div class="term"><div class="term__circle">3<small>years</small></div><div class="term__cost"><sup>$</sup>396</div></div>
        <div class="term"><div class="term__circle">2<small>years</small></div><div class="term__cost"><sup>$</sup>264</div></div>
        <p class="terms__note">Multi-year payment locks in current rates</p>
      </div>
    </div>
    <p class="price__note">&nbsp;</p>
    <div class="schedule">
      <p class="schedule__label">Weeding &amp; trimming on your gravesite</p>
      <p class="schedule__text">Approximately every 7 weeks during the growing season mid-April through mid-October</p>
    </div>
    <ul class="features">
      <li>Payment Ensures<br>Grave Care Forever</li>
      <li>Monument Leveling</li>
      <li>Monument Cleaning</li>
      <li>Full Bed Of Boxwood Shrubs</li>
      <li>Replacement Of Shrubs</li>
      <li>Trust Certificate</li>
    </ul>
  </section>

  <section class="card card--perpetual">
    <span class="ribbon">Most popular</span>
    <header class="card__head">
      <h2 class="card__title">Perpetual Care<br>Endowment</h2>
      <p class="card__sub">Landscaping care forever<br>for graves with plantings</p>
    </header>
    <div class="price">
      <p class="price__label">12 monthly<br>payments of</p>
      <p class="price__amount"><sup>$</sup>351</p>
    </div>
    <p class="price__note">Call for single payment discount</p>
    <div class="schedule">
      <p class="schedule__label">Weeding &amp; trimming on your gravesite</p>
      <p class="schedule__text">Approximately every 7 weeks during the growing season mid-April through mid-October</p>
    </div>
    <ul class="features">
      <li class="is-included">Payment Ensures<br>Grave Care Forever</li>
      <li class="is-included">Monument Leveling</li>
      <li class="is-included">Monument Cleaning</li>
      <li class="is-included">Full Bed Of Boxwood Shrubs</li>
      <li class="is-included">Replacement Of Shrubs</li>
      <li class="is-included">Trust Certificate</li>
    </ul>
  </section>

  <section class="card card--basic">
    <header class="card__head">
      <h2 class="card__title">Basic Care<br>Endowment</h2>
      <p class="card__sub">Landscaping care forever<br>for graves with no plantings</p>
    </header>
    <div class="price">
      <p class="price__label">12 monthly<br>payments of</p>
      <p class="price__amount"><sup>$</sup>287</p>
    </div>
    <p class="price__note">Call for single payment discount</p>
    <div class="schedule">
      <p class="schedule__label">Weeding &amp; trimming on your gravesite</p>
      <p class="schedule__text">2 times per year:<br>mid-May &amp; mid-September</p>
    </div>
    <ul class="features">
      <li class="is-included">Payment Ensures<br>Grave Care Forever</li>
      <li class="is-included">Monument Leveling</li>
      <li class="is-included">Monument Cleaning</li>
      <li>Full Bed Of Boxwood Shrubs</li>
      <li>Replacement Of Shrubs</li>
      <li>Trust Certificate</li>
    </ul>
  </section>

  <div class="brand"><span class="brand__dot"></span><span>Hollowbrook Memorial</span></div>
  <ul class="contact">
    <li class="phone"><svg viewBox="0 0 24 24" aria-hidden="true"><path d="M6.6 10.8a15 15 0 0 0 6.6 6.6l2.2-2.2c.3-.3.7-.4 1-.2 1.1.4 2.3.6 3.6.6.6 0 1 .4 1 1V20c0 .6-.4 1-1 1A17 17 0 0 1 3 4c0-.6.4-1 1-1h3.5c.6 0 1 .4 1 1 0 1.2.2 2.4.6 3.6.1.3 0 .7-.2 1z" fill="none" stroke="#8e1f33" stroke-width="2"/></svg>(201) 555-0148</li>
    <li><svg viewBox="0 0 24 24" aria-hidden="true"><rect x="3" y="5" width="18" height="14" fill="none" stroke="#8e1f33" stroke-width="2"/><path d="M3 6l9 7 9-7" fill="none" stroke="#8e1f33" stroke-width="2"/></svg>info@hollowbrookmemorial.org</li>
    <li><svg viewBox="0 0 24 24" aria-hidden="true"><circle cx="12" cy="12" r="9" fill="none" stroke="#8e1f33" stroke-width="2"/><path d="M3 12h18M12 3c3 3 3 15 0 18M12 3c-3 3-3 15 0 18" fill="none" stroke="#8e1f33" stroke-width="1.6"/></svg>www.hollowbrookmemorial.org</li>
  </ul>

  <figure class="proof proof--before">
    <div class="proof__photo" role="img" aria-label="Before care photo: overgrown gravesite with untrimmed shrubs"></div>
    <figcaption class="proof__tag">Before Care</figcaption>
  </figure>
  <figure class="proof proof--after">
    <div class="proof__photo" role="img" aria-label="After care photo: neatly trimmed gravesite with boxwood shrubs"></div>
    <figcaption class="proof__tag">After care</figcaption>
  </figure>
</main>
</body>
</html>
```